Request for Business Card Design

Hi. My name is Marlene, I am looking for a new business card design for my company, Quarrow Signal Instruments, LLC. I really like the design you did for Tarsel Venture and was hoping you could do something similar using our full logo and our mark. I am also open to any raised texture design using our mark. I have attached our full logo, which would need to be somewhere on the card, as well as the mark in both outline and full form, as well as our brand colors / guide. The card does not have to be white, as long as our logo and mark appear. I actually like darker colored business cards more, but am open to all options. If you are interested in working with me, please let me know. We would also take the business card design into letterhead design if you can do that.

```html
<!DOCTYPE html>
<html lang="en">
<head>
<meta charset="utf-8">
<title>Quarrow Signal Instruments – Business Card</title>
<link rel="stylesheet" href="https://fonts.googleapis.com/css2?family=Saira:wght@700;800&family=Arimo:wght@400&display=swap">
<style>
  :root {
    --backdrop: #141414;
    --card-white: #f7f7f5;
    --card-dark: #232323;
    --card-dark-deep: #1b1b1b;
    --brand-blue: #0a93b8;
    --ink: #161616;
    --ink-soft: #555555;
    --paper-white: #ffffff;
  }
  * { margin: 0; padding: 0; box-sizing: border-box; }
  html, body { width: 1200px; height: 963px; overflow: hidden; }
  body {
    background: var(--backdrop);
    position: relative;
    font-family: "Arimo", Arial, sans-serif;
  }
  .card {
    position: absolute;
    left: 280px;
    width: 640px;
    height: 366px;
    border-radius: 24px;
    border-bottom: 4px solid var(--brand-blue);
    overflow: hidden;
  }
  .card--front { top: 95px; background: var(--card-white); }
  .card--back { top: 501px; background: var(--card-dark); }

  /* wordmark */
  .wordmark { position: absolute; font-family: "Saira", sans-serif; font-weight: 800; }
  .wordmark__name { display: block; letter-spacing: 3px; line-height: 1.15; }
  .wordmark__tagline { display: block; letter-spacing: 1.2px; line-height: 1.2; margin-top: 2px; }
  .card--front .wordmark { right: 44px; top: 60px; color: var(--ink); }
  .card--front .wordmark__name { font-size: 46px; }
  .card--front .wordmark__tagline { font-size: 12px; }
  .card--back .wordmark { left: 48px; top: 140px; color: var(--paper-white); }
  .card--back .wordmark__name { font-size: 54px; }
  .card--back .wordmark__tagline { font-size: 14px; }
  .wordmark-dot {
    position: absolute; left: 318px; top: 44px;
    width: 36px; height: 36px; border-radius: 50%;
    background: var(--brand-blue);
  }

  /* holder */
  .holder { position: absolute; left: 44px; top: 126px; }
  .holder__name {
    font-family: "Saira", sans-serif; font-weight: 800;
    font-size: 21px; letter-spacing: 0.5px; color: var(--brand-blue);
    text-transform: uppercase; line-height: 1.2;
  }
  .holder__role { font-size: 15px; color: var(--ink-soft); margin-top: 2px; }
  .divider {
    position: absolute; left: 40px; top: 192px;
    width: 500px; height: 1.5px; background: var(--brand-blue);
  }
  .contact { position: absolute; left: 44px; top: 208px; list-style: none; }
  .contact li {
    display: flex; align-items: center; gap: 10px;
    font-size: 15px; color: var(--ink-soft); margin-bottom: 9px;
  }
  .contact svg { width: 14px; height: 14px; flex: none; }
  .address {
    position: absolute; right: 100px; top: 262px;
    text-align: right; font-size: 15px; line-height: 1.45; color: var(--ink-soft);
  }

  /* back decoration */
  .back-disc {
    position: absolute; right: -60px; top: 40px;
    width: 340px; height: 340px; border-radius: 50%;
    background: radial-gradient(circle at 40% 35%, #2c2c2c, var(--card-dark-deep));
    box-shadow: inset 0 2px 3px rgba(255,255,255,0.06);
  }
</style>
</head>
<body>
  <section class="card card--front" aria-label="Business card front">
    <span class="wordmark-dot"></span>
    <div class="wordmark">
      <span class="wordmark__name">QUARROW</span>
      <span class="wordmark__tagline">SIGNAL INSTRUMENTS</span>
    </div>

    <div class="holder">
      <p class="holder__name">Marlene Hartwell</p>
      <p class="holder__role">Manager</p>
    </div>
    <div class="divider"></div>

    <ul class="contact">
      <li>
        <svg viewBox="0 0 16 16" aria-hidden="true"><path fill="#0a93b8" d="M3.6 1.5l2.2 2.6-1.3 1.6c.9 2 2.3 3.5 4.3 4.4l1.6-1.3 2.6 2.2-1.2 2.3C6.6 13.2 2.8 9.4 1.3 3.2z"/></svg>
        123-456-2100
      </li>
      <li>
        <svg viewBox="0 0 16 16" aria-hidden="true"><rect x="1.5" y="3.5" width="13" height="9" fill="none" stroke="#0a93b8" stroke-width="1.5"/><path d="M1.5 3.5L8 9l6.5-5.5" fill="none" stroke="#0a93b8" stroke-width="1.5"/></svg>
        youremail@mailhost.com
      </li>
      <li>
        <svg viewBox="0 0 16 16" aria-hidden="true"><circle cx="8" cy="8" r="6.5" fill="none" stroke="#0a93b8" stroke-width="1.4"/><ellipse cx="8" cy="8" rx="2.8" ry="6.5" fill="none" stroke="#0a93b8" stroke-width="1.2"/><path d="M1.5 8h13M2.5 4.8h11M2.5 11.2h11" stroke="#0a93b8" stroke-width="1.1"/></svg>
        www.yourwebsite.com
      </li>
    </ul>

    <p class="address">Your Address, City<br>State, Zip 0000</p>
  </section>

  <section class="card card--back" aria-label="Business card back">
    <span class="back-disc"></span>
    <div class="wordmark">
      <span class="wordmark__name">QUARROW</span>
      <span class="wordmark__tagline">SIGNAL INSTRUMENTS</span>
    </div>
  </section>
</body>
</html>
```